Sophisticated, clean website reflecting my feminine, playful side to sell my abstract art,

I need a website no more than 3 pages to showcase my paintings, a little about me and some contact info. I do abstracts so looking for something a little edgy, yet feminine and current.
Updates

Hi there, These are some artists websites that I Iike: Marnelvoss.com (I like how airy it is) peterwallombry.com garethpolvens.com (I like how it scrolls) I'll need a place for a photo ( a headshot-i do not have it yet so I'll need to be able to upload that later) as well as an area for my bio. Also, it's important that I will be able to upload any new photos and descriptions easily so it should be user friendly. Lastly, I like in a sunny place so would like to have this seem upbeat and playful as that is how i like to paint. thanks-I'm trying to upload my photos now -

Target Market(s)

ppl ages 35-70 who want large scale art for their homes

Industry/Entity Type

art

Coding

Coded - Design and coding required

Number of Pages Required

3 page

Colors

Designer to choose colors to be used in the design.

Requirements
Must have
• photos of my art, a place for my bio, be easy to reach me. tasteful-nothing too "in your face" -my clients are pretty high end and organized. They like clean lines
Nice to have
• sophisticated background, muted tones in the back-similar clean font throughout-no cursive
Should not have
• too many dark areas. Too many blocks of color. Too serious.

```html
<!DOCTYPE html>
<html lang="en">
<head>
<meta charset="utf-8">
<title>Lena Marlowe — About</title>
<link href="https://fonts.googleapis.com/css2?family=Oswald:wght@300;400&family=Baloo+2:wght@400;500&display=swap" rel="stylesheet">
<style>
  :root {
    --ink: #111111;
    --text: #222222;
    --muted: #555555;
    --rule: #8a8a8a;
    --paper: #ffffff;
    --photo-light: #dfe4e8;
    --photo-mid: #c9cfd4;
    --photo-warm: #d9c7bc;
  }
  html, body {
    margin: 0;
    padding: 0;
    width: 1200px;
    height: 858px;
    overflow: hidden;
    background: var(--paper);
  }
  .page {
    position: relative;
    width: 1200px;
    height: 858px;
    color: var(--text);
    font-family: "Baloo 2", sans-serif;
  }
  .brand {
    position: absolute;
    top: 25px;
    left: 0;
    width: 1200px;
    display: flex;
    justify-content: center;
    align-items: center;
    gap: 13px;
    font-family: "Oswald", sans-serif;
    font-weight: 300;
    font-size: 15px;
    letter-spacing: 0.5px;
    color: var(--ink);
  }
  .brand-square {
    width: 54px;
    height: 67px;
    background: var(--ink);
  }
  .brand-rule {
    position: absolute;
    top: 109px;
    left: 514px;
    width: 172px;
    height: 1px;
    background: var(--rule);
  }
  .main-nav {
    position: absolute;
    top: 131px;
    left: 0;
    width: 1200px;
    font-family: "Oswald", sans-serif;
    font-weight: 300;
    font-size: 20px;
    color: var(--muted);
  }
  .main-nav a {
    position: absolute;
    color: inherit;
    text-decoration: none;
    line-height: 30px;
  }
  .main-nav a.is-current { color: var(--ink); font-weight: 400; }
  .nav-gallery { left: 452px; }
  .nav-about { left: 575px; }
  .nav-contact { left: 686px; }
  .headshot {
    position: absolute;
    top: 242px;
    left: 42px;
    width: 401px;
    height: 512px;
    border: 2px solid var(--ink);
    background: linear-gradient(180deg, var(--photo-light) 0%, var(--photo-mid) 55%, var(--photo-warm) 100%);
  }
  .bio {
    position: absolute;
    top: 344px;
    left: 485px;
    width: 405px;
  }
  .bio-text {
    margin: 0;
    font-size: 13.4px;
    line-height: 21px;
    color: var(--text);
  }
  .bio-points {
    list-style: none;
    margin: 12px 0 0;
    padding: 0;
    font-size: 13.4px;
    line-height: 27px;
    color: var(--ink);
    font-weight: 500;
  }
  .bio-points li {
    position: relative;
    padding-left: 17px;
  }
  .bio-points li::before {
    content: "";
    position: absolute;
    left: 0;
    top: 10px;
    width: 8px;
    height: 8px;
    border-radius: 50%;
    background: var(--ink);
  }
  .contact-email {
    position: absolute;
    top: 580px;
    left: 485px;
    display: flex;
    align-items: center;
    gap: 10px;
    font-size: 13.4px;
    color: var(--text);
  }
  .social-links {
    position: absolute;
    top: 622px;
    left: 485px;
    display: flex;
    gap: 25px;
  }
  .social-dot {
    width: 27px;
    height: 27px;
    border: 1.5px solid var(--ink);
    border-radius: 50%;
  }
  .site-footer {
    position: absolute;
    top: 826px;
    left: 0;
    width: 1200px;
    text-align: center;
    font-size: 11px;
    color: var(--text);
  }
</style>
</head>
<body>
<div class="page">
  <header>
    <div class="brand">
      <span>LENA</span>
      <span class="brand-square"></span>
      <span>MARLOWE</span>
    </div>
    <div class="brand-rule"></div>
    <nav class="main-nav">
      <a class="nav-gallery" href="#">GALLERY</a>
      <a class="nav-about is-current" href="#">ABOUT</a>
      <a class="nav-contact" href="#">CONTACT</a>
    </nav>
  </header>

  <main>
    <div class="headshot" role="img" aria-label="Headshot of the artist against a pale grey wall"></div>

    <section class="bio">
      <p class="bio-text">Lorem ipsum dolor sit amet, consectetuer adipiscing elit. Aenean commodo ligula eget dolor. Aenean massa. Cum sociis natoque penatibus et magnis dis parturient montes, nascetur ridiculus mus. Donec quam felis, ultricies nec, pellentesque eu, pretium quis, sem. Nulla consequat massa quis enim.</p>
      <ul class="bio-points">
        <li>Donec pede justo, fringilla vel, aliquet nec, vulputate eget, arcu.</li>
        <li>In enim justo, rhoncus ut, imperdiet a, venenatis vitae, justo.</li>
        <li>Aenean leo ligula, porttitor eu, consequat vitae, eleifend ac, enim.</li>
      </ul>
    </section>

    <div class="contact-email">
      <svg width="18" height="13" viewBox="0 0 18 13" aria-hidden="true">
        <rect x="0" y="0" width="18" height="13" rx="1.5" fill="#111111"/>
        <path d="M1 1.5 L9 7.5 L17 1.5" fill="none" stroke="#ffffff" stroke-width="1.4"/>
      </svg>
      <span>contact@LenaMarloweAbstract.com</span>
    </div>

    <div class="social-links">
      <span class="social-dot" aria-label="Social profile"></span>
      <span class="social-dot" aria-label="Social profile"></span>
    </div>
  </main>

  <footer class="site-footer">©2022 Lena Marlowe Art. All rights reserved.</footer>
</div>
</body>
</html>
```